WordPress Site That Reviews Footwear

We need a wordpress web design for an affiliate site called PaceKite. We review and do roundups on footwear products. The final design should be clean and mobile friendly. The site should be built with Gutenberg page builder. We like the design of https://lunavessel.com/.
Updates

Need extra days to review

Target Market(s)

USA

Industry/Entity Type

Footwear

Logo Text

PaceKite

Number of Pages Required

4 page

Font styles to use
Serif
Sans Serif

Requirements
Must have
• Wordpress site
Blog post
Page
Categories
Homepage

```html
<!DOCTYPE html>
<html lang="en">
<head>
<meta charset="utf-8">
<title>PaceKite — Footwear Reviews</title>
<link href="https://fonts.googleapis.com/css2?family=Jost:wght@300;400;500;600&display=swap" rel="stylesheet">
<style>
:root{
  --coral:#f86a60;
  --coral-soft:#fbd3cf;
  --ink:#2a2a2a;
  --muted:#8a8a8a;
  --grey-band:#f1f1f1;
  --card:#e9e9e9;
  --white:#ffffff;
  --footer:#262626;
  --footer-text:#bdbdbd;
}
*{box-sizing:border-box;margin:0;padding:0}
html,body{width:1200px;height:2784px;overflow:hidden}
body{font-family:"Jost",sans-serif;color:var(--ink);background:var(--white);position:relative}
a{color:inherit;text-decoration:none}
.btn{display:inline-block;background:var(--coral);color:var(--white);font-size:13px;font-weight:500;letter-spacing:.5px;padding:12px 24px;border-radius:2px}
.section-title{font-size:34px;font-weight:500;text-align:center;letter-spacing:1px;line-height:1.2}
.section-sub{font-size:13px;color:var(--muted);text-align:center;line-height:1.5;width:520px;margin:10px auto 0}

/* hero */
.hero{position:absolute;left:0;top:0;width:1200px;height:640px;overflow:hidden}
.hero-arc{position:absolute;left:0;top:0}
.brand{position:absolute;left:180px;top:34px;font-size:20px;letter-spacing:3px;color:var(--coral);font-weight:500}
.nav{position:absolute;right:180px;top:36px;display:flex;gap:42px;font-size:12px;font-weight:500;letter-spacing:1px}
.hero-text{position:absolute;left:180px;top:210px;width:330px}
.hero-text h1{font-size:30px;font-weight:400;line-height:1.4;letter-spacing:.3px;white-space:nowrap}
.hero-text h1 strong{font-weight:500}
.hero-text .btn{margin-top:30px}
.hero-shoes{position:absolute;left:525px;top:330px;width:360px;height:160px;border-radius:80px 90px 40px 40px;background:radial-gradient(ellipse at 45% 55%,#5b3a24 0%,#2d1d14 55%,#eeeae6 80%,transparent 82%)}
.review-pop{position:absolute;width:150px;background:var(--white);border-radius:6px;box-shadow:0 6px 18px rgba(0,0,0,.12);padding:12px 14px;font-size:9px;line-height:1.5;color:var(--muted)}
.review-pop b{display:block;color:var(--ink);font-size:10px;font-weight:600}
.review-pop .stars{color:var(--coral);font-size:9px}
.pop-a{left:590px;top:108px}
.pop-b{left:780px;top:112px}
.pop-dot{position:absolute;width:28px;height:28px;border-radius:50%;background:#c9b3a5;border:3px solid var(--white)}

/* know */
.know{position:absolute;left:0;top:640px;width:1200px;height:680px;background:var(--grey-band)}
.know .section-title{margin-top:28px}
.know-panel{position:absolute;left:0;top:160px;width:880px;height:440px;background:var(--coral);border-radius:0 40px 40px 0}
.know-grid{position:absolute;left:180px;top:70px;display:grid;grid-template-columns:230px 230px;column-gap:50px;row-gap:90px;color:var(--white)}
.know-item h3{font-size:16px;font-weight:500;margin-bottom:8px}
.know-item p{font-size:11px;line-height:1.55;opacity:.9}
.know-item .more{display:flex;align-items:center;gap:8px;font-size:11px;margin-top:10px}
.know-item .more i{width:22px;height:22px;border-radius:50%;background:var(--white);display:inline-block}
.know-photo{position:absolute;left:760px;top:220px;width:250px;height:250px;border-radius:50%;border:6px solid var(--white);background:radial-gradient(circle at 50% 40%,#d8d4d0 0%,#8f8b88 55%,#3b3a3a 100%)}

/* results */
.results{position:absolute;left:0;top:1320px;width:1200px;height:320px}
.results .section-title{margin-top:12px}
.result-row{position:absolute;left:180px;top:130px;display:flex;gap:20px}
.result-card{width:266px;height:140px;background:var(--card);border-radius:8px;padding:20px 18px}
.result-card h3{font-size:14px;font-weight:500;margin-bottom:8px}
.result-card p{font-size:10.5px;color:var(--muted);line-height:1.5}
.result-card i{display:block;width:22px;height:22px;border-radius:50%;background:var(--coral);margin-top:10px}

/* experts */
.experts{position:absolute;left:0;top:1640px;width:1200px;height:410px;background:var(--grey-band)}
.experts-intro{position:absolute;left:180px;top:90px;width:190px}
.experts-intro h2{font-size:34px;font-weight:500;line-height:1.12}
.experts-intro p{font-size:10.5px;color:var(--muted);line-height:1.5;margin-top:14px}
.experts-intro .btn{margin-top:26px}
.posts{position:absolute;left:390px;top:70px;display:flex;gap:20px}
.post{width:190px}
.post-img{height:110px;border-radius:4px}
.post-meta{font-size:9px;color:var(--muted);margin-top:12px}
.post h3{font-size:14px;font-weight:500;line-height:1.3;margin-top:6px}
.post .more{display:flex;align-items:center;gap:6px;font-size:10px;color:var(--coral);margin-top:10px}
.post .more i{width:16px;height:16px;border-radius:50%;background:var(--coral);display:inline-block}

/* reviews */
.reviews{position:absolute;left:0;top:2050px;width:1200px;height:390px}
.reviews .section-title{margin-top:30px}
.review-row{position:absolute;left:180px;top:140px;display:flex;gap:20px}
.review-card{width:195px;height:200px;background:var(--card);border-radius:6px;padding:20px 16px}
.reviewer{display:flex;gap:10px;align-items:center}
.reviewer i{width:36px;height:36px;border-radius:50%;background:#b9a99d;display:block}
.reviewer b{font-size:12px;font-weight:600;display:block}
.reviewer span{font-size:9px;color:var(--muted)}
.review-card .stars{color:var(--coral);font-size:13px;margin:12px 0 8px;letter-spacing:1px}
.review-card p{font-size:10px;color:var(--muted);line-height:1.55}

/* footer */
.footer{position:absolute;left:0;top:2440px;width:1200px;height:344px;background:var(--footer);color:var(--footer-text)}
.footer-brand{position:absolute;left:180px;top:150px;font-size:18px;letter-spacing:1px;color:var(--white);font-weight:500}
.footer-cols{position:absolute;left:350px;top:56px;display:flex;gap:50px}
.footer-col{width:130px;font-size:11px}
.footer-col h4{font-size:12px;color:var(--white);font-weight:500;letter-spacing:1px;margin-bottom:16px}
.footer-col li{list-style:none;margin-bottom:14px}
.contact li{display:flex;gap:8px;align-items:center}
.contact svg{flex:none}
.socials{display:flex;gap:10px;align-items:center}
.socials i{width:12px;height:12px;border-radius:50%;background:var(--footer-text);display:inline-block}
.footer-bar{position:absolute;left:0;bottom:0;width:1200px;height:46px;border-top:1px solid #3a3a3a;text-align:center;line-height:46px;font-size:10px}
.footer-bar b{color:var(--coral);font-weight:400}
</style>
</head>
<body>

<header class="hero">
  <svg class="hero-arc" width="1200" height="640" aria-hidden="true">
    <path d="M200 640 Q 600 380 1080 520" fill="none" stroke="#f3d8d5" stroke-width="1.5"/>
    <path d="M700 60 Q 1200 80 1160 640" fill="none" stroke="#ececec" stroke-width="1.5"/>
  </svg>
  <a class="brand" href="#">PACEKITE</a>
  <nav class="nav"><a href="#">HOME</a><a href="#">PAGES</a><a href="#">BLOG</a><a href="#">CONTACT</a></nav>
  <div class="hero-text">
    <h1>WE REVIEW AND<br>DO ROUNDUPS ON<br><strong>FOOTWEAR PRODUCTS</strong></h1>
    <a class="btn" href="#">KNOW MORE</a>
  </div>
  <div class="hero-shoes" role="img" aria-label="Pair of polished leather dress shoes"></div>
  <div class="review-pop pop-a"><b>Vivamus cursus</b><span class="stars">★★★★★</span><br>Lorem ipsum dolor sit amet, consectetur adipiscing elit nunc.</div>
  <div class="review-pop pop-b"><b>Vivamus cursus</b><span class="stars">★★★★★</span><br>Lorem ipsum dolor sit amet, consectetur adipiscing elit nunc.</div>
  <span class="pop-dot" style="left:716px;top:184px"></span>
  <span class="pop-dot" style="left:800px;top:206px"></span>
</header>

<section class="know">
  <h2 class="section-title">KNOW ABOUT YOUR SHOES</h2>
  <p class="section-sub">Vivamus cursus maximus turpis vel feugiat. Phasellus sem arcu, bibendum id condimentum eu, volutpat vitae turpis. Maecenas auctor erat nibh.</p>
  <div class="know-panel">
    <div class="know-grid">
      <div class="know-item"><h3>Ut et dolor ac liber</h3><p>Lorem ipsum dolor sit amet consectetur adipiscing elit sed do eiusmod tempor.</p><a class="more" href="#">Read More <i></i></a></div>
      <div class="know-item"><h3>Ut et dolor ac liber</h3><p>Lorem ipsum dolor sit amet consectetur adipiscing elit sed do eiusmod tempor.</p><a class="more" href="#">Read More <i></i></a></div>
      <div class="know-item"><h3>Ut et dolor ac liber</h3><p>Lorem ipsum dolor sit amet consectetur adipiscing elit sed do eiusmod tempor.</p><a class="more" href="#">Read More <i></i></a></div>
      <div class="know-item"><h3>Ut et dolor ac liber</h3><p>Lorem ipsum dolor sit amet consectetur adipiscing elit sed do eiusmod tempor.</p><a class="more" href="#">Read More <i></i></a></div>
    </div>
  </div>
  <div class="know-photo" role="img" aria-label="Man in a suit seated on a chair"></div>
</section>

<section class="results">
  <h2 class="section-title">FINAL RESULTS</h2>
  <p class="section-sub">Vivamus cursus maximus turpis vel feugiat. Phasellus sem arcu, bibendum id condimentum eu, volutpat vitae turpis. Maecenas auctor erat nibh.</p>
  <div class="result-row">
    <div class="result-card"><h3>Integer quis vehicula</h3><p>Ut et dolor ac libero gravida tempus. Nulla venenatis condimentum tellus.</p><i></i></div>
    <div class="result-card"><h3>Integer quis vehicula</h3><p>Ut et dolor ac libero gravida tempus. Nulla venenatis condimentum tellus.</p><i></i></div>
    <div class="result-card"><h3>Integer quis vehicula</h3><p>Ut et dolor ac libero gravida tempus. Nulla venenatis condimentum tellus.</p><i></i></div>
  </div>
</section>

<section class="experts">
  <div class="experts-intro">
    <h2>Learn from<br>the Experts</h2>
    <p>Ut et dolor ac libero gravida tempus. Nulla venenatis condimentum tellus.</p>
    <a class="btn" href="#">KNOW MORE</a>
  </div>
  <div class="posts">
    <article class="post"><div class="post-img" role="img" aria-label="Team meeting around a table" style="background:linear-gradient(135deg,#8d8f93,#c7c3bd)"></div><p class="post-meta">Kedit con — May 18, 2021</p><h3>Vivamus id felis luctus tin ciduntt venenatis</h3><a class="more" href="#">Read More <i></i></a></article>
    <article class="post"><div class="post-img" role="img" aria-label="Colleagues talking in an office" style="background:linear-gradient(135deg,#a19a92,#5d6168)"></div><p class="post-meta">Kedit con — May 18, 2021</p><h3>Vivamus id felis luctus tin ciduntt venenatis</h3><a class="more" href="#">Read More <i></i></a></article>
    <article class="post"><div class="post-img" role="img" aria-label="Group working on laptops" style="background:linear-gradient(135deg,#b7b2aa,#6f7a86)"></div><p class="post-meta">Kedit con — May 18, 2021</p><h3>Vivamus id felis luctus tin ciduntt venenatis</h3><a class="more" href="#">Read More <i></i></a></article>
  </div>
</section>

<section class="reviews">
  <h2 class="section-title">CLIENT REVIEWS</h2>
  <div class="review-row">
    <div class="review-card"><div class="reviewer"><i></i><div><b>S. Marlow</b><span>Verified buyer</span></div></div><div class="stars">★★★★★</div><p>Lorem ipsum dolor sit amet, consectetur adipiscing elit. Nulla venenatis condimentum tellus.</p></div>
    <div class="review-card"><div class="reviewer"><i></i><div><b>D. Pruitt</b><span>Verified buyer</span></div></div><div class="stars">★★★★★</div><p>Lorem ipsum dolor sit amet, consectetur adipiscing elit. Nulla venenatis condimentum tellus.</p></div>
    <div class="review-card"><div class="reviewer"><i></i><div><b>K. Hollis</b><span>Verified buyer</span></div></div><div class="stars">★★★★★</div><p>Lorem ipsum dolor sit amet, consectetur adipiscing elit. Nulla venenatis condimentum tellus.</p></div>
    <div class="review-card"><div class="reviewer"><i></i><div><b>J. Tovey</b><span>Verified buyer</span></div></div><div class="stars">★★★★★</div><p>Lorem ipsum dolor sit amet, consectetur adipiscing elit. Nulla venenatis condimentum tellus.</p></div>
  </div>
</section>

<footer class="footer">
  <div class="footer-brand">PACEKITE</div>
  <div class="footer-cols">
    <ul class="footer-col"><h4>COMPANY</h4><li>Terms of Use</li><li>Privacy Policy</li><li>Editorial Policy</li><li>How We Rate Items</li></ul>
    <ul class="footer-col"><h4>DISCOVER</h4><li>Terms of Use</li><li>Privacy Policy</li><li>Editorial Policy</li><li>How We Rate Items</li></ul>
    <ul class="footer-col"><h4>ABOUT</h4><li>About</li><li>Contact</li><li>Media</li></ul>
    <ul class="footer-col contact" style="width:170px"><h4>CONTACT INFO</h4>
      <li><svg width="12" height="12" viewBox="0 0 24 24"><path fill="#f86a60" d="M6.6 10.8a15 15 0 006.6 6.6l2.2-2.2c.3-.3.7-.4 1-.2 1.1.4 2.3.6 3.6.6.6 0 1 .4 1 1V20c0 .6-.4 1-1 1A17 17 0 013 4c0-.6.4-1 1-1h3.5c.6 0 1 .4 1 1 0 1.2.2 2.4.6 3.6.1.3 0 .7-.2 1z"/></svg>+1 555 0148 22</li>
      <li><svg width="12" height="12" viewBox="0 0 24 24"><path fill="#f86a60" d="M12 2a7 7 0 00-7 7c0 5 7 13 7 13s7-8 7-13a7 7 0 00-7-7zm0 9.5a2.5 2.5 0 110-5 2.5 2.5 0 010 5z"/></svg>48 Ridge Ave, Austin</li>
      <li><svg width="12" height="12" viewBox="0 0 24 24"><path fill="#f86a60" d="M3 5h18v14H3zm2 2v.5l7 4.5 7-4.5V7z"/></svg>hello@pacekite.com</li>
      <li class="socials">Social <i></i><i></i><i></i></li>
    </ul>
  </div>
  <div class="footer-bar">© 2021 <b>PaceKite</b>. All Rights Reserved.</div>
</footer>

</body>
</html>
```